kolvarin.link kolvarin.space kolvarin.press website

The website is named KOLVARIN and it will have 3 domain names. kolvarin.link, press, space.
I'd like it to be viewed on Pads, pcs and phones.

page menu:

kolvarin.link(start page): presentation of company. (creative, design, app, new product innovation.)
Here we'll need sosial media icons: plimber, vendoloop, mirtavel, trelvanet. (light but some 'fruity' colors)

kolvarin.press: blog. It will be a 75% picture blog > rest will be text. I need to be able to resize pictures and shape columns to picture size. (light but some 'fruity' colors)

kolvarin.space : the fun part of this web design, however, on entering the page I'd like a non-disclosure agreement where viewer simply click "yes, I agree" after filling out contact info. (check attached document)
We will have space here for uploading PDF files viewers can download. There is also a blog space here to tell in brief about the PDF file. (maybe a space/sci-fi theme her e.g spacechimp, Laika the space dog?)

I will attach the logo here I want you to use > and develop for the .space .press webpage. The logo i uploaded is for the .link page.

Target Market(s)

venture capitalists

Number of Pages Required

3 page

Requirements
Must have
• a few 'fruity colors' but mostly white and grey

```html
<!DOCTYPE html>
<html lang="en">
<head>
<meta charset="utf-8">
<title>Kolvarin Link — We Design &amp; Develop Your Dreams</title>
<link rel="stylesheet" href="https://fonts.googleapis.com/css2?family=Exo+2:wght@500;600&family=Lato:ital,wght@0,400;0,700;1,400&family=Dancing+Script:wght@600&display=swap">
<style>
  :root {
    --ink: #1d1d1d;
    --body-text: #333333;
    --header-bg: #f8f8f8;
    --services-bg: #fdf9f1;
    --lemon: #f6ec1f;
    --orange: #f07c1b;
    --leaf: #5e9a3a;
    --leaf-dark: #2f6b2a;
    --tomato: #d83a2a;
    --footer-darker: #2b2b2b;
    --rule: #e8dfd0;
    --white: #ffffff;
  }
  * { box-sizing: border-box; margin: 0; padding: 0; }
  html, body { width: 946px; height: 1200px; overflow: hidden; }
  body { position: relative; background: var(--white); font-family: "Lato", Arial, sans-serif; color: var(--body-text); }

  .site-header { position: absolute; left: 0; top: 0; width: 946px; height: 108px; background: var(--header-bg); border-bottom: 1px solid #e2e2e2; }
  .brand { position: absolute; display: flex; align-items: center; gap: 6px; font-family: "Exo 2", sans-serif; font-weight: 600; color: var(--ink); letter-spacing: 1px; white-space: nowrap; }
  .brand__mark { width: 12px; height: 12px; background: var(--lemon); }
  .site-header .brand { left: 78px; top: 38px; font-size: 22px; }

  .social { position: absolute; display: flex; gap: 10px; list-style: none; white-space: nowrap; }
  .social li { display: flex; align-items: center; gap: 4px; font-size: 10px; font-weight: 700; color: #4d4d4d; }
  .social i { display: block; width: 8px; height: 8px; border-radius: 2px; }
  .social .c1 { background: #3b5a9a; } .social .c2 { background: #29a9e1; }
  .social .c3 { background: #0f77b5; } .social .c4 { background: #8a6b55; }
  .site-header .social { right: 78px; top: 24px; }

  .contact-strip { position: absolute; right: 132px; top: 66px; display: flex; gap: 24px; font-size: 14px; color: var(--ink); white-space: nowrap; }
  .contact-strip span { display: flex; align-items: center; gap: 8px; }
  .menu-toggle { position: absolute; left: 831px; top: 62px; width: 37px; height: 27px; border: 1px solid #c9c9c9; background: var(--white); }
  .menu-toggle i { position: absolute; left: 7px; width: 22px; height: 2px; background: var(--ink); }

  .hero { position: absolute; left: 0; top: 108px; width: 946px; height: 372px; background: radial-gradient(ellipse at 60% 30%, #5f6f5c 0%, #4a3d2e 45%, #2c2219 100%); }
  .hero__title { position: absolute; top: 152px; width: 100%; text-align: center; font-family: "Exo 2", sans-serif; font-weight: 600; font-size: 26px; color: var(--white); }
  .hero__cta { position: absolute; left: 418px; top: 199px; width: 108px; height: 32px; background: var(--lemon); border-radius: 2px; font-family: "Exo 2", sans-serif; font-weight: 600; font-size: 14px; color: var(--ink); display: flex; align-items: center; justify-content: center; }
  .hero__dots { position: absolute; top: 342px; left: 447px; display: flex; gap: 7px; }
  .hero__dots i { width: 11px; height: 11px; border-radius: 50%; background: var(--white); }
  .hero__dots i.active { background: var(--tomato); box-shadow: inset 0 0 0 2px var(--white); }

  .services { position: absolute; left: 0; top: 480px; width: 946px; height: 340px; background: var(--services-bg); }
  .service { position: absolute; top: 50px; width: 250px; }
  .service__image { height: 151px; border-top: 3px solid; box-shadow: 0 10px 10px -6px rgba(0,0,0,.25); }
  .service h2 { margin: 24px 0 0 2px; font-family: "Exo 2", sans-serif; font-weight: 500; font-size: 17px; color: var(--ink); }
  .service p { margin: 8px 0 0 2px; font-size: 10.3px; line-height: 15px; color: var(--body-text); }
  .service--design { left: 78px; } .service--design .service__image { border-color: var(--leaf); background: linear-gradient(160deg, #ffd52a, #f7bd12 60%, #efefe7 90%); }
  .service--app { left: 348px; } .service--app .service__image { border-color: var(--orange); background: linear-gradient(140deg, #5b93d3, #4a7fbd); }
  .service--innovation { left: 618px; } .service--innovation .service__image { border-color: var(--tomato); background: radial-gradient(circle at 55% 70%, #c9f2ff 0%, #2b7e96 25%, #0e2d3f 75%); }

  .about { position: absolute; left: 0; top: 862px; width: 946px; text-align: center; }
  .about h2 { font-family: "Exo 2", sans-serif; font-weight: 600; font-size: 21px; color: var(--ink); }
  .about h2 .o { color: var(--orange); } .about h2 .y { color: #f5e43a; }
  .about__rule { position: relative; width: 250px; height: 1px; margin: 17px auto 0; background: var(--rule); }
  .about__rule i { position: absolute; left: 118px; top: -8px; width: 14px; height: 16px; border-radius: 50%; background: #e89a1c; }
  .about p { width: 724px; margin: 24px auto 0; font-size: 11.3px; line-height: 19.4px; color: var(--ink); }

  .signup-bar { position: absolute; left: 0; top: 1048px; width: 946px; height: 62px; background: var(--leaf); border-top: 3px solid var(--leaf-dark); }
  .signup { position: absolute; left: 78px; top: 18px; display: flex; align-items: center; }
  .signup input { width: 234px; height: 22px; border: 0; padding-left: 7px; margin-left: 8px; font-family: "Lato", sans-serif; font-size: 9.5px; color: #444; }
  .signup button { width: 27px; height: 22px; border: 0; background: var(--tomato); color: var(--white); font-family: "Lato", sans-serif; font-weight: 700; font-size: 9.5px; }
  .signup-bar .brand { left: 440px; top: 19px; font-size: 15px; color: var(--white); }
  .signup-bar .brand__mark { width: 10px; height: 10px; }
  .follow { position: absolute; left: 558px; top: 19px; font-family: "Dancing Script", cursive; font-size: 13px; color: var(--white); white-space: nowrap; }
  .signup-bar .social { right: 78px; top: 24px; gap: 8px; }
  .signup-bar .social li { color: var(--white); font-size: 9px; }

  .site-footer { position: absolute; left: 0; top: 1110px; width: 946px; height: 90px; background: linear-gradient(#444, var(--footer-darker)); color: var(--white); font-size: 9.5px; }
  .footer-contacts { position: absolute; top: 16px; left: 0; width: 100%; display: flex; justify-content: center; gap: 32px; list-style: none; white-space: nowrap; }
  .footer-contacts li { display: flex; align-items: center; gap: 7px; }
  .copyright { position: absolute; top: 59px; width: 100%; text-align: center; }
</style>
</head>
<body>

<header class="site-header">
  <div class="brand"><span class="brand__mark"></span>KOLVARIN</div>
  <ul class="social">
    <li><i class="c1"></i>mirtavel</li><li><i class="c2"></i>plimber</li><li><i class="c3"></i>trelvanet</li><li><i class="c4"></i>vendoloop</li>
  </ul>
  <div class="contact-strip">
    <span><svg width="16" height="16" viewBox="0 0 16 16"><path d="M3 1l3 3-2 2c1 2 3 4 5 5l2-2 3 3-2 3C6 14 2 10 1 3z" fill="#d83a2a"/></svg>123-456-7890</span>
    <span><svg width="20" height="14" viewBox="0 0 20 14"><rect x="0.5" y="0.5" width="19" height="13" fill="#d83a2a"/><path d="M1 1l9 7 9-7" stroke="#fff" stroke-width="1.4" fill="none"/></svg>info@kolvarinlink.com</span>
  </div>
  <div class="menu-toggle"><i style="top:8px"></i><i style="top:12px"></i><i style="top:16px"></i></div>
</header>

<section class="hero" role="img" aria-label="Photo of a designer's desk with a laptop showing a web design page, sketches and coffee">
  <h1 class="hero__title">WE DESIGN &amp; DEVELOP YOUR DREAMS</h1>
  <a class="hero__cta">CONTACT US</a>
  <div class="hero__dots"><i></i><i class="active"></i><i></i></div>
</section>

<section class="services">
  <article class="service service--design">
    <div class="service__image" role="img" aria-label="Illustration of a yellow desk with a computer monitor and design tools"></div>
    <h2>CREATIVE DESIGN</h2>
    <p>Ut wisi enim ad minim veniam, quis nostrud exercimli tation ullamcorper suscipit lobortis nisl ut aliquip exm ea commodo consequat.</p>
  </article>
  <article class="service service--app">
    <div class="service__image" role="img" aria-label="Illustration of hands using tablets and phones with app screens on a blue background"></div>
    <h2>APP DEVELOPMENT</h2>
    <p>Ut wisi enim ad minim veniam, quis nostrud exercimli tation ullamcorper suscipit lobortis nisl ut aliquip exm ea commodo consequat.</p>
  </article>
  <article class="service service--innovation">
    <div class="service__image" role="img" aria-label="Photo of hanging light bulbs with one glowing brightly"></div>
    <h2>NEW PRODUCT INNOVATION</h2>
    <p>Ut wisi enim ad minim veniam, quis nostrud exercimli tation ullamcorper suscipit lobortis nisl ut aliquip exm ea commodo consequat.</p>
  </article>
</section>

<section class="about">
  <h2><span class="o">ABOUT</span> KOLVARIN <span class="y">LINK</span></h2>
  <div class="about__rule"><i></i></div>
  <p>Lorem ipsum dolor sit amet, consectetuer adipiscing elit, sed diam nonummy nibh euismod tincidunt ut laoreet dolore magna aliquam erat volutpat. Ut wisi enim ad minim veniam, quis nostrud exerci tation ullamcorper suscipit lobortis nisl ut aliquip ex ea commodo consequat. Duis autem vel eum iriure dolor in hendrerit in vulputate velit esse molestie consequat, vel illum dolore eu feugiat nulla facilisis at vero eros et accumsan et iusto odio dignissim qui blandit praesent luptatum zzril delenit augue duis dolore te feugait nulla facilisi.</p>
</section>

<section class="signup-bar">
  <form class="signup">
    <svg width="21" height="20" viewBox="0 0 21 20"><path d="M1 8l9.5-7 9.5 7v11H1z" fill="none" stroke="#fff" stroke-width="1.4"/><path d="M1 8l9.5 6 9.5-6" fill="none" stroke="#fff" stroke-width="1.4"/></svg>
    <input type="email" placeholder="Enter Your Email Here">
    <button type="button">GO</button>
  </form>
  <div class="brand"><span class="brand__mark"></span>KOLVARIN</div>
  <span class="follow">Follow Us On</span>
  <ul class="social">
    <li><i class="c1"></i>mirtavel</li><li><i class="c2"></i>plimber</li><li><i class="c3"></i>trelvanet</li><li><i class="c4"></i>vendoloop</li>
  </ul>
</section>

<footer class="site-footer">
  <ul class="footer-contacts">
    <li><svg width="8" height="11" viewBox="0 0 8 11"><path d="M4 0a4 4 0 0 1 4 4c0 3-4 7-4 7S0 7 0 4a4 4 0 0 1 4-4z" fill="#fff"/><circle cx="4" cy="4" r="1.5" fill="#3b3b3b"/></svg>Contrary to popular belief, Lorem Ipsum is.</li>
    <li><svg width="10" height="10" viewBox="0 0 16 16"><path d="M3 1l3 3-2 2c1 2 3 4 5 5l2-2 3 3-2 3C6 14 2 10 1 3z" fill="#fff"/></svg>Phone: 123-456-7890</li>
    <li><svg width="13" height="9" viewBox="0 0 20 14"><rect width="20" height="14" fill="#fff"/><path d="M1 1l9 7 9-7" stroke="#3b3b3b" stroke-width="1.6" fill="none"/></svg>Email: info@kolvarinlink.com</li>
    <li><svg width="12" height="11" viewBox="0 0 12 11"><rect x="3" y="0" width="6" height="4" fill="#fff"/><rect x="0" y="4" width="12" height="5" rx="1" fill="#fff"/><rect x="3" y="7" width="6" height="4" fill="#ccc"/></svg>Fax: 123-456-7890</li>
  </ul>
  <p class="copyright">Copyright © 2016 Kolvarin Link. All Rights Reserved.</p>
</footer>

</body>
</html>
```